Service Transporter Design // Vehicle Branding Project*

We need a sticker design for our service vehicle based on our current one (see attached) for a company based in Berlin Germany called KORFF Grossküchentechnik. We are selling professional industrial kitchen equipment.

Vehicle Type: Velmora Traxel M

We would like the design to be edgy and confident. We would prefer the sticker design to utilize the colors on our logo (see attached). White is the color of the vehicle.

Please take a closer look to file 3, a sample which we like!

Furthermore, we would be glad to jump on new trend like transport our business with the help of icons or symbols i.e. a shopping cart icon for our online shop.

In addition for that, we are looking for a service technician in our city.
Therefore it would be helpful to place a banner (3 sides) for it with the following information:

Kollege gesucht
Bewerbungen erwünscht!

in addition to that

Telephon: 030 / 71 28 94 3 57
Email: service@korff-kuechenhaus.de
Shop: www.korff-kuechenhaus.de
24h

Our company has been one of the well-known and powerful companies in our industry in Berlin and Brandenburg. It was founded in 1926 as a trade company for heating systems and oriented after 1945 to the field of cooking equipment for commercial kitchens.

The purchased in 30 years of service expertise, we have developed into a leader in the engineering industry, food service in Berlin and could extend this position even after the reunification of the surrounding area in the state of Brandenburg.

Our ambition is not to be the cheapest provider in the lowest-price segment. Our mission is to provide our partners with well-known, enduring brand makes and accompanying maintenance service, the basic conditions for a long-term economic success.

We utilize the expertise of powerful manufacturing companies with long experience in concretizing of caterers.

We would like the sticker to be modern, clean and professional, and should utilize the colors cyan white and grey.

Our website is: http://www.korff-kuechenhaus.de

Your are welcome to impress us!

Reason: not 100% percent conviced of the current work. please do better and give you best! Thank you

sorry, no one wins, no design we are looking for

Hello Designers!

Please be welcome again to make a Design in this direction combined with our new logo:

Reason: Hello Designers! Your welcome again to precise the Car Design as mentioned in my comments with the blue & white example please make some stunning designs! thx! wolfram

please take a closer look on sample design file:

Today of have a meeting about all your design proposals.
Will give you feedback by today.

Thx, Wolfram

Hallo Designer,

 

First of all, thank so much for the nice ideas from you!

We made ??yesterday comprehensive thoughts about the designconcept of our service vehicles and have come to the conclusion that we reallywant to communicate our brand more "KORFF".

 

How do we imagine the now proposing?

The logo we want to be more larger at all on the vehicle.

Our business fields are more stroken by icons/symbols on thesideview and backview.

topics:

REPERATURSERVICE(repair service) KOCHGERÄTE (coookingmachines) – KÜHLGERÄTE (cooling machines)– SPÜLMSCHINEN (professional dishwaher) - if there is more room, you canplace also a coffeemchines (professional one)

for each topic we need a
pregnant symbol, butwith no comparison to home machines>> industrial machines.

please have a look on attached new Pdf for the concept of content

I will extent the project for more 7 days, I would be very thankfull, if you provide me a new direction :-)

Thank you!

Wolfram

Reason: Hallo Designer, First of all, thank so much for the nice ideas from you! We made yesterday comprehensive thoughts about the design concept of our service vehicles and have come to the conclusion that we really want to communicate our brand more "KORFF". How do we imagine the now proposing? The logo we want to be more larger at all on the vehicle. Our business fields are more stroken by icons/symbols on the sideview and backview. topics: REPERATURSERVICE (repair service) KOCHGERÄTE (coookingmachines) – KÜHLGERÄTE (cooling machines) – SPÜLMSCHINEN (professional dishwaher) - if there is more room, you can place also a coffeemchines (professional one) for each topic we need a pregnant symbol, but with no comparison to home machines >> industrial machines. please be so kind and read new additional concept in pdf

Target Market(s)

Hotels, Hospital, Restaurants, professional kitchen

Industry/Entity Type

Industrial

Requirements
Must have
• all in our colors:
white (I know, it not a color, cyan (like in logo file) and grey

icons & symbols
Nice to have
• impressive Photo, eye catcher

```html
<!DOCTYPE html>
<html lang="de">
<head>
<meta charset="utf-8">
<title>KORFF Grossküchentechnik – Fahrzeugbeschriftung</title>
<link rel="stylesheet" href="https://fonts.googleapis.com/css2?family=Roboto+Condensed:wght@400;700&family=Open+Sans:wght@400&family=Pinyon+Script&display=swap">
<style>
  :root {
    --cyan: #1a9ad6;
    --grey: #7a7a7a;
    --grey-text: #6b6b6b;
    --white: #ffffff;
    --yellow: #ffd400;
    --backdrop: #e9e9e9;
  }
  * { margin: 0; padding: 0; box-sizing: border-box; }
  html, body { width: 1200px; height: 900px; overflow: hidden; }
  body { background: var(--backdrop); position: relative; font-family: "Roboto Condensed", sans-serif; }

  .chef-photo { position: absolute; left: 800px; top: 232px; width: 340px; height: 358px; z-index: 0;
    background: linear-gradient(120deg, #f2f2f2 0%, #d9d4cc 45%, #8a6e55 75%, #5d4a3b 100%);
    border-radius: 0 18px 0 0; }

  .services-panel { position: absolute; left: 498px; top: 230px; width: 360px; height: 128px; z-index: 2; }
  .services-panel svg.panel-bg { position: absolute; inset: 0; }
  .service { position: absolute; display: flex; align-items: center; gap: 8px; white-space: nowrap;
    color: var(--white); font-weight: 700; font-size: 13px; }
  .service svg { width: 28px; height: 24px; }

  .slogan { position: absolute; left: 512px; top: 360px; z-index: 2; font-family: "Pinyon Script", cursive;
    color: var(--cyan); font-size: 40px; transform: rotate(-4deg); transform-origin: left bottom; white-space: nowrap; }

  .brand { position: absolute; left: 540px; top: 400px; z-index: 2; display: flex; align-items: center; gap: 20px; }
  .brand-mark { width: 46px; height: 46px; background: var(--cyan); }
  .brand-name { font-weight: 700; font-size: 84px; color: var(--cyan); letter-spacing: 18px; line-height: 1; }

  .tagline { position: absolute; left: 548px; top: 510px; z-index: 2; font-family: "Open Sans", sans-serif;
    color: var(--grey-text); font-size: 27px; letter-spacing: 11.5px; white-space: nowrap; }
  .tagline-rule { position: absolute; left: 548px; top: 546px; width: 476px; height: 2px; background: var(--cyan); z-index: 2; }

  .contact-panel { position: absolute; left: 548px; top: 562px; width: 324px; height: 118px; z-index: 2; }
  .contact-panel svg.panel-bg { position: absolute; inset: 0; }
  .contact-line { position: absolute; top: 14px; display: flex; align-items: center; gap: 5px; white-space: nowrap;
    color: var(--white); font-size: 13px; }
  .contact-line svg { width: 14px; height: 12px; }
  .shop { position: absolute; left: 20px; top: 38px; display: flex; align-items: flex-start; gap: 8px; color: var(--white); }
  .shop svg { width: 48px; height: 40px; margin-top: 6px; }
  .shop-label { font-size: 16px; line-height: 1.1; }
  .shop-url { font-size: 19px; font-weight: 700; line-height: 1.3; white-space: nowrap; }

  .hiring-bubble { position: absolute; left: 220px; top: 476px; width: 160px; height: 100px; }
  .hiring-bubble svg { position: absolute; inset: 0; }
  .hiring-text { position: absolute; left: 0; top: 14px; width: 150px; text-align: center;
    font-weight: 700; font-size: 15px; line-height: 1.1; color: var(--white); }
  .hiring-text .hl { color: var(--yellow); display: block; }

  .service-mobile { position: absolute; left: 388px; top: 506px; width: 66px; text-align: center;
    color: var(--cyan); font-weight: 700; line-height: 1; }
  .service-mobile .hours { font-size: 32px; }
  .service-mobile .label { font-size: 13px; display: block; letter-spacing: 0.3px; }
</style>
</head>
<body>

  <div class="chef-photo" role="img" aria-label="Foto: Koch in weißer Kochjacke mit verschränkten Armen vor einer Großküche mit Kombidämpfer und Töpfen"></div>

  <section class="services-panel" aria-label="Leistungen">
    <svg class="panel-bg" viewBox="0 0 360 128" preserveAspectRatio="none"><polygon points="0,0 360,0 345,112 14,128" fill="var(--grey)"/></svg>

    <div class="service" style="left:30px;top:18px">
      <svg viewBox="0 0 28 24" fill="none" stroke="var(--cyan)" stroke-width="2"><path d="M3 16h22M6 16v4h16v-4M9 4c-2 3 2 4 0 8M14 4c-2 3 2 4 0 8M19 4c-2 3 2 4 0 8"/></svg>
      Kochgeräte</div>
    <div class="service" style="left:166px;top:18px">
      <svg viewBox="0 0 28 24" fill="var(--cyan)"><rect x="2" y="6" width="20" height="14" rx="2"/><path d="M22 9h3v6h-3" stroke="var(--cyan)" stroke-width="2" fill="none"/></svg>
      Kuchenmaschinen</div>
    <div class="service" style="left:38px;top:50px">
      <svg viewBox="0 0 28 24" fill="none" stroke="var(--cyan)" stroke-width="2"><path d="M3 8h22M6 8v-4h16v4M7 12v2M12 12v4M17 12v2M22 12v4M9 18v2M19 18v2"/></svg>
      Spumaschinen</div>
    <div class="service" style="left:192px;top:50px">
      <svg viewBox="0 0 24 24" fill="var(--cyan)"><circle cx="12" cy="12" r="7"/><circle cx="12" cy="12" r="3" fill="var(--grey)"/><path d="M11 1h2v4h-2zM11 19h2v4h-2zM1 11h4v2H1zM19 11h4v2h-4z"/></svg>
      Kaffeemaschinen</div>
    <div class="service" style="left:80px;top:82px">
      <svg viewBox="0 0 24 24" fill="none" stroke="var(--cyan)" stroke-width="2"><path d="M12 2v20M3 7l18 10M21 7L3 17"/></svg>
      Kuhlgeräte</div>
    <div class="service" style="left:216px;top:82px">
      <svg viewBox="0 0 24 24" fill="none" stroke="var(--cyan)" stroke-width="3" stroke-linecap="round"><path d="M4 20L14 10"/><path d="M14 10a5 5 0 1 0 4-6l-3 3 2 2 3-3" stroke-width="2"/></svg>
      Service</div>
  </section>

  <p class="slogan">Wir kommen morgen!</p>

  <div class="brand">
    <span class="brand-mark"></span>
    <span class="brand-name">KORFF</span>
  </div>
  <p class="tagline">Grossküchentechnik</p>
  <div class="tagline-rule"></div>

  <section class="contact-panel" aria-label="Kontakt">
    <svg class="panel-bg" viewBox="0 0 324 118" preserveAspectRatio="none"><polygon points="0,6 324,0 320,118 6,118" fill="var(--grey)"/></svg>
    <div class="contact-line" style="left:12px">
      <svg viewBox="0 0 14 12" fill="var(--white)"><path d="M2 1l3 0 1 3-2 1c1 2 2 3 4 4l1-2 3 1v3c-6 0-10-4-10-10z"/></svg>
      030 / 71 28 94 3 57</div>
    <div class="contact-line" style="left:138px">
      <svg viewBox="0 0 14 12" fill="none" stroke="var(--white)" stroke-width="1.4"><rect x="1" y="1" width="12" height="10"/><path d="M1 1l6 5 6-5"/></svg>
      service@korff-kuechenhaus.de</div>
    <div class="shop">
      <svg viewBox="0 0 48 40" fill="none" stroke="var(--white)" stroke-width="2.5" stroke-linejoin="round"><path d="M2 4h7l6 22h26l5-16H12"/><circle cx="18" cy="34" r="3"/><circle cx="38" cy="34" r="3"/><path d="M20 14v8M26 14v8M32 14v8M38 14v8" stroke-width="2"/></svg>
      <div>
        <div class="shop-label">Shop Online</div>
        <div class="shop-url">www.korff-kuechenhaus.de</div>
      </div>
    </div>
  </section>

  <div class="hiring-bubble">
    <svg viewBox="0 0 160 100"><ellipse cx="76" cy="46" rx="76" ry="44" fill="var(--cyan)"/><polygon points="120,76 156,98 138,66" fill="var(--cyan)"/></svg>
    <p class="hiring-text"><span class="hl">KOLLEGE</span><span class="hl">GESUCHT</span>Bewerbungen<br>erwünscht!</p>
  </div>

  <div class="service-mobile">
    <span class="hours">24h</span>
    <span class="label">SERVICE</span>
    <span class="label">MOBIL</span>
  </div>

</body>
</html>
```